RK Donnelly & Associates

Create a website encompassing design work already carried out for business card.
Small accounting practice, business accounting and management, superannuation, audit, taxation.

```html
<!DOCTYPE html>
<html lang="en">
<head>
<meta charset="utf-8">
<title>RK Donnelly &amp; Associates</title>
<link rel="stylesheet" href="https://fonts.googleapis.com/css2?family=Roboto:wght@400;500&family=Lato:wght@400;700&display=swap">
<style>
:root{
  --page:#2a2a2a;
  --panel:#111111;
  --footer:#222222;
  --base:#141414;
  --accent:#5b9bd5;
  --accent-light:#7fb8ea;
  --accent-dark:#3f7fc0;
  --text:#ffffff;
  --muted:#d8d8d8;
  --nav-top:#3b3b3b;
  --nav-bottom:#262626;
}
*{box-sizing:border-box;margin:0;padding:0}
html,body{width:980px;height:1200px;overflow:hidden}
body{background:var(--page);font-family:"Roboto",sans-serif;color:var(--text);position:relative}
.abs{position:absolute}

/* header */
.brand{left:196px;top:16px;display:flex;align-items:center;gap:8px}
.brand-mark{width:22px;height:22px;background:var(--accent)}
.brand-name{font-family:"Roboto",sans-serif;font-weight:500;font-size:16px;color:var(--text);line-height:1.1;width:110px}
.tagline{left:137px;top:73px;width:231px;height:16px;background:var(--accent);font-size:6px;font-weight:500;line-height:16px;padding-left:8px;white-space:nowrap}
.phone{left:545px;top:46px;display:flex;align-items:center;gap:6px;font-size:15px}
.search{left:668px;top:41px;width:170px;height:28px;display:flex}
.search-field{flex:1;background:#fff;color:#444;font-size:11px;line-height:28px;padding-left:10px}
.search-btn{width:29px;background:var(--accent);display:flex;align-items:center;justify-content:center}

/* nav */
.nav{left:136px;top:100px;width:706px;height:51px;display:flex;background:linear-gradient(var(--nav-top),var(--nav-bottom))}
.nav-item{font-size:13px;line-height:51px;text-align:center;border-right:1px solid #1c1c1c}
.nav-item.active{background:linear-gradient(var(--accent-light),var(--accent))}

/* slider */
.slider{left:136px;top:151px;width:706px;height:363px;background:linear-gradient(120deg,#9a9fa6 0%,#6d6f74 45%,#3e3b3c 100%)}
.slide-arrow{top:146px;width:29px;height:29px;border-radius:50%;background:rgba(40,40,40,.8);display:flex;align-items:center;justify-content:center}
.slide-caption{left:300px;top:262px;width:320px;text-align:center;font-size:21px;font-weight:500;line-height:34px;text-shadow:0 1px 3px #000}

/* welcome */
.welcome{left:136px;top:516px;width:706px;height:156px;background:var(--panel);text-align:center}
.welcome h1{font-size:17px;font-weight:400;color:var(--accent-light);margin-top:17px}
.welcome p{font-size:10px;line-height:19px;width:640px;margin:10px auto 0}
.btn{display:inline-block;background:linear-gradient(var(--accent-light),var(--accent));border:1px solid var(--accent-dark);color:#fff}
.btn-small{margin-top:13px;width:84px;height:25px;line-height:23px;font-size:8px}

/* services */
.card{top:679px;width:228px;height:250px;background:var(--panel);text-align:center}
.card-photo{width:199px;height:106px;margin:17px auto 0}
.card h2{font-size:12px;font-weight:500;color:var(--accent-light);margin-top:15px}
.card p{font-size:10px;line-height:18px;width:180px;margin:8px auto 0}
.btn-more{margin-top:10px;width:95px;height:29px;line-height:27px;font-size:12px}

/* footer */
.footer{left:0;top:950px;width:980px;height:184px;background:var(--footer)}
.foot-col{top:26px}
.foot-col h3{font-size:14px;font-weight:400;color:var(--accent-light);margin-bottom:18px}
.foot-col p,.foot-col li{font-family:"Lato",sans-serif;font-size:8px;line-height:15px;color:var(--muted)}
.contact{left:143px;width:170px}
.contact .detail{margin-top:12px}
.news{left:393px;width:180px}
.news-item{display:flex;gap:8px;margin-bottom:18px}
.news-thumb{width:49px;height:41px;border:2px solid #ddd;background:linear-gradient(#8a9098,#3d4147)}
.news-title{font-family:"Lato",sans-serif;font-size:9px;font-weight:700;color:#eee;margin-top:3px}
.news-date{font-family:"Lato",sans-serif;font-size:8px;color:#ddd;margin-top:6px}
.newsletter{left:619px;width:220px}
.newsletter p{font-family:"Roboto",sans-serif;font-size:10px;line-height:17px;color:#eee}
.signup{display:flex;height:27px;margin-top:11px}
.signup-field{flex:1;background:#fff;color:#888;font-size:9px;line-height:27px;padding-left:9px}
.signup-btn{width:46px;background:var(--accent);font-size:9px;font-weight:500;line-height:27px;text-align:center}
.social{display:flex;gap:9px;margin-top:17px}
.social span{width:24px;height:24px;border-radius:50%;border:2px solid #3a3a3a}
.base{left:0;top:1134px;width:980px;height:66px;background:var(--base);text-align:center;font-size:10px;line-height:66px}
</style>
</head>
<body>

<header>
  <div class="abs brand"><span class="brand-mark"></span><span class="brand-name">RK Donnelly &amp; Associates</span></div>
  <div class="abs tagline">Accountant · Business Solutions · Management · Superannuation · Audit</div>
  <div class="abs phone">
    <svg width="16" height="16" viewBox="0 0 16 16"><circle cx="8" cy="8" r="7" fill="none" stroke="#5b9bd5" stroke-width="1.4"/><path d="M5.5 4.5l1.5 1.5-.8 1a5 5 0 0 0 2.8 2.8l1-.8 1.5 1.5-1 1c-3 0-6-3-6-6z" fill="#5b9bd5"/></svg>
    <span>555-214-3370</span>
  </div>
  <div class="abs search">
    <div class="search-field">Search..</div>
    <div class="search-btn"><svg width="14" height="14" viewBox="0 0 14 14"><circle cx="5.5" cy="5.5" r="4" fill="none" stroke="#fff" stroke-width="1.6"/><path d="M8.5 8.5l4 4" stroke="#fff" stroke-width="1.8"/></svg></div>
  </div>
</header>

<nav class="abs nav">
  <div class="nav-item active" style="width:71px">Home</div>
  <div class="nav-item" style="width:85px">About us</div>
  <div class="nav-item" style="width:82px">Service</div>
  <div class="nav-item" style="width:68px">Audit</div>
  <div class="nav-item" style="width:114px">Management</div>
  <div class="nav-item" style="width:104px">Accounting</div>
  <div class="nav-item" style="width:70px">News</div>
  <div class="nav-item" style="width:112px;border-right:0">Contact us</div>
</nav>

<section class="abs slider" role="img" aria-label="Photo of three colleagues working together at an office computer">
  <div class="abs slide-arrow" style="left:15px"><svg width="10" height="14"><path d="M8 1L2 7l6 6" fill="none" stroke="#aaa" stroke-width="1.5"/></svg></div>
  <div class="abs slide-arrow" style="left:660px"><svg width="10" height="14"><path d="M2 1l6 6-6 6" fill="none" stroke="#aaa" stroke-width="1.5"/></svg></div>
  <div class="abs slide-caption">LOREM IPSUM IS SIMPLY DUMMY PRINTING AND TYPESETTING</div>
</section>

<section class="abs welcome">
  <h1>WELCOME RK DONNELLY &amp; ASSOCIATES</h1>
  <p>Lorem Ipsum is simply dummy text of the printing and typesetting industry. Lorem Ipsum has been the industry's standard dummy text ever since the 1500s, when an unknown printer took a galley of type and scrambled it to make a type specimen book. It has survived not only five centuries, but also the leap into electronic typesetting, remaining essentially unchanged</p>
  <span class="btn btn-small">READ MORE</span>
</section>

<section class="abs card" style="left:136px">
  <div class="card-photo" role="img" aria-label="Overhead photo of a team planning around a desk" style="background:linear-gradient(135deg,#d9dde2,#8e949c)"></div>
  <h2>ACCOUNTING PRACTICE</h2>
  <p>Lorem Ipsum is simply dummy text of the printing and typesetting industry.</p>
  <span class="btn btn-more">MORE</span>
</section>
<section class="abs card" style="left:373px">
  <div class="card-photo" role="img" aria-label="Photo of a business team standing before a globe" style="background:linear-gradient(#4a95b8,#123244)"></div>
  <h2>BUSINESS ACCOUNTING</h2>
  <p>Lorem Ipsum is simply dummy text of the printing and typesetting industry.</p>
  <span class="btn btn-more">MORE</span>
</section>
<section class="abs card" style="left:613px">
  <div class="card-photo" role="img" aria-label="Photo of business people meeting and shaking hands" style="background:linear-gradient(90deg,#8c8c8c,#d4d0cc)"></div>
  <h2>SUPERANNUATION</h2>
  <p>Lorem Ipsum is simply dummy text of the printing and typesetting industry.</p>
  <span class="btn btn-more">MORE</span>
</section>

<footer class="abs footer">
  <div class="abs foot-col contact">
    <h3>CONTACT INFO</h3>
    <p>Lorem ipsum dolor sit amet, consectetur adipisicing elit, sed do eiusmod tempor incididunt ut labore et dolore magna aliqua.</p>
    <p class="detail">(555) 0142 337016</p>
    <p class="detail" style="margin-top:7px">info@rkdonnelly-mail.com</p>
  </div>
  <div class="abs foot-col news">
    <h3>LATEST NEWS</h3>
    <div class="news-item"><div class="news-thumb" role="img" aria-label="News photo"></div><div><div class="news-title">Corvan recieve award</div><div class="news-date">july 7, 2014</div></div></div>
    <div class="news-item"><div class="news-thumb" role="img" aria-label="News photo"></div><div><div class="news-title">Corvan recieve award</div><div class="news-date">july 7, 2014</div></div></div>
  </div>
  <div class="abs foot-col newsletter">
    <h3>NEWSLETTER</h3>
    <p>Join our mailing list to stay up to date and get notices about our new releases!</p>
    <div class="signup"><div class="signup-field">mail@example.com</div><div class="signup-btn">JOIN</div></div>
    <div class="social">
      <span style="background:#3fb4e5"></span><span style="background:#3b5fb0"></span><span style="background:#555"></span><span style="background:#e0508c"></span>
    </div>
  </div>
</footer>

<div class="abs base">© Copyright 2014 &nbsp; All Rights Reserved</div>

</body>
</html>
```